New letter head for Air Conditioning business

We need a new professional letter head design to suit our new re-branded air conditioning business. Our new logo is attached

```html
<!DOCTYPE html>
<html lang="en">
<head>
<meta charset="utf-8">
<title>Coralen Letterhead</title>
<link href="https://fonts.googleapis.com/css2?family=Questrial&display=swap" rel="stylesheet">
<style>
  :root {
    --paper: #efefef;
    --ink: #2b2b2b;
    --ink-soft: #3a3a3a;
    --green: #4fb06f;
    --red: #e0544c;
    --white: #ffffff;
  }
  * { margin: 0; padding: 0; box-sizing: border-box; }
  html, body { width: 971px; height: 1200px; overflow: hidden; }
  body {
    background: var(--paper);
    font-family: "Questrial", "Century Gothic", sans-serif;
    color: var(--ink-soft);
    position: relative;
  }
  .letterhead { position: absolute; inset: 0; }

  .brand { position: absolute; left: 55px; top: 64px; display: flex; align-items: center; gap: 14px; }
  .brand-dot { width: 44px; height: 44px; border-radius: 50%; background: var(--green); }
  .brand-name { font-size: 40px; letter-spacing: 4px; color: var(--ink); line-height: 1; }
  .brand-tagline { font-size: 9.5px; letter-spacing: 1.2px; color: var(--green); margin-top: 6px; }

  .contact-address {
    position: absolute; right: 362px; top: 76px;
    text-align: right; font-size: 15px; line-height: 18px; color: var(--ink);
  }
  .contact-divider { position: absolute; left: 625px; top: 78px; width: 2px; height: 48px; background: var(--green); }
  .contact-list { position: absolute; left: 641px; top: 76px; list-style: none; font-size: 15px; line-height: 18px; color: var(--ink); }
  .contact-list li { display: flex; align-items: center; gap: 8px; }
  .contact-list svg { width: 11px; height: 11px; fill: var(--red); }

  .recipient { position: absolute; left: 55px; top: 292px; font-size: 15px; line-height: 24.5px; color: var(--ink); }

  .letter-body { position: absolute; left: 55px; top: 406px; width: 861px; font-size: 15.5px; line-height: 24.5px; text-align: justify; color: var(--ink); }
  .letter-body p + p { margin-top: 27px; }
  .letter-body p.tight { margin-top: 22px; }

  .closing { position: absolute; left: 55px; top: 827px; font-size: 15px; color: var(--ink); }
  .signature-area {
    position: absolute; left: 55px; top: 856px; width: 176px; height: 60px;
    background: linear-gradient(90deg, #d9d9d9, #e8e8e8);
  }

  .footer { position: absolute; left: 0; bottom: 0; width: 971px; height: 42px; }
  .footer-url {
    position: absolute; left: 560px; bottom: 12px; font-size: 16px; color: var(--white);
    display: flex; align-items: center; gap: 8px;
  }
  .footer-url svg { width: 12px; height: 12px; fill: var(--white); }
</style>
</head>
<body>
<div class="letterhead">
  <header>
    <div class="brand">
      <div class="brand-dot"></div>
      <div>
        <div class="brand-name">CORALEN</div>
        <div class="brand-tagline">AIR CONDITIONING &amp; REFRIGERATION</div>
      </div>
    </div>

    <address class="contact-address" style="font-style:normal">
      4410 W. Harbor Lane,<br>Suite 208 Fallbrook,<br>CA 92031
    </address>
    <div class="contact-divider"></div>
    <ul class="contact-list">
      <li><svg viewBox="0 0 12 12"><path d="M2.5 0.5l2 2.5-1.2 1.3c.7 1.6 2 2.9 3.4 3.6L8 6.6l2.5 2-1.3 2.4C4.8 10.6 1.4 7.2 1 2.3z"/></svg>555-310-2284</li>
      <li><svg viewBox="0 0 12 12"><path d="M3 0h6v3H3zM1 4h10v5H9v3H3V9H1zM4 8v3h4V8z"/></svg>555-310-2290</li>
      <li><svg viewBox="0 0 12 12"><path d="M0 2h12v8H0zM1 3l5 3.5L11 3z" fill-rule="evenodd"/></svg>hello@coralenair.com</li>
    </ul>
  </header>

  <div class="recipient">
    Mr/s<br>First Name and Last Name<br>Company Name<br>Address
  </div>

  <main class="letter-body">
    <p>Lorem Ipsum is simply dummy text of the printing and typesetting industry. Lorem Ipsum has been the industry's standard dummy text ever since the 1500s, when an unknown printer took a galley of type and scrambled it to make a type specimen book. It has survived not only five centuries, but also the leap into electronic typesetting, remaining essentially unchanged. It was popularised in the 1960s with the release of Letraset sheets containing Lorem Ipsum passages.</p>
    <p>he standard chunk of Lorem Ipsum used since the 1500s is reproduced below for those interested. Sections 1.10.32 and 1.10.33 from "de Finibus Bonorum et Malorum" by Cicero are also reproduced in their exact original form, accompanied by English versions from the 1914 translation by H. Rackham. Lorem ipsum dolor sit amet, consectetur adipiscing elit, sed do eiusmod tempor incididunt ut labore et dolore magna aliqua.</p>
    <p class="tight">It is a long established fact that a reader will be distracted by the readable content of a page when looking at its layout. The point of using Lorem Ipsum is that it has a more-or-less normal distribution of letters, as opposed to using 'Content here, content here', making it look like readable English. Many desktop publishing packages and web page editors now .</p>
  </main>

  <div class="closing">Your Sincerely,</div>
  <div class="signature-area" role="img" aria-label="Handwritten signature"></div>

  <footer class="footer">
    <svg width="971" height="42" viewBox="0 0 971 42">
      <rect x="0" y="31" width="971" height="11" fill="var(--green)"/>
      <polygon points="496,42 528,0 866,0 898,42" fill="var(--white)"/>
      <polygon points="503,42 532,3 862,3 891,42" fill="var(--red)"/>
    </svg>
    <div class="footer-url">
      <svg viewBox="0 0 12 12"><circle cx="6" cy="6" r="6"/></svg>
      www.coralenair.com
    </div>
  </footer>
</div>
</body>
</html>
```